Bramblewick Homes Tarrow Customer Brochure

Need a brochure designed that is clean and minimal that contains our logo, and contact information. Would like an area where we could insert business cards, and slips on both sides of the openings to place sheets of paper in. Would prefer to have the COVER LETTER I have attached printed on one side of the opening.

Target Market(s)

Home buyers

Font styles to use
Sans Serif

Colors

Designer to choose colors to be used in the design.

Requirements
Must have
• Logo, contact info, website, etc. Must be minimal in design and very clean looking.
Nice to have
• Please see above
Should not have
• No stock pictures of homes, builds, etc. Need it to look very clean

```html
<!DOCTYPE html>
<html lang="en">
<head>
<meta charset="utf-8">
<title>Bramblewick Homes Tarrow – Brochure and Letterhead</title>
<link rel="stylesheet" href="https://fonts.googleapis.com/css2?family=Lato:wght@400;700;900&display=swap">
<style>
  :root {
    --stage: #cbcbcb;
    --tan: #d2a77a;
    --tan-light: #e0c09c;
    --charcoal: #333333;
    --ink: #2b2b2b;
    --paper: #ffffff;
    --label: #2a2a2a;
  }
  * { box-sizing: border-box; margin: 0; padding: 0; }
  html, body { width: 1200px; height: 1200px; overflow: hidden; }
  body { background: var(--stage); font-family: "Lato", sans-serif; position: relative; }

  .view-label { position: absolute; font-size: 29px; color: var(--label); font-weight: 400; white-space: nowrap; transform: translateX(-50%); }
  .view-label--front { left: 382px; top: 40px; }
  .view-label--back { left: 382px; top: 617px; }
  .view-label--letterhead { left: 970px; top: 622px; }

  .sheet { position: absolute; background: var(--paper); box-shadow: 3px 5px 6px rgba(0,0,0,0.28); overflow: hidden; }
  .brochure { width: 658px; height: 468px; left: 69px; }
  .brochure--front { top: 102px; }
  .brochure--back { top: 677px; height: 470px; }
  .letterhead { left: 809px; top: 675px; width: 333px; height: 469px; }

  .panel-tan { position: absolute; left: 0; top: 0; width: 330px; height: 100%; background: var(--tan); }
  .deco { position: absolute; left: 0; top: 0; width: 100%; height: 100%; }

  /* Brand name block */
  .brand { position: absolute; display: flex; flex-direction: column; align-items: center; transform: translateX(-50%); }
  .brand-mark { background: var(--charcoal); }
  .brand-name { font-weight: 900; color: var(--charcoal); text-transform: uppercase; text-align: center; line-height: 1.05; letter-spacing: 0.02em; }
  .brand--cover { left: 490px; top: 150px; }
  .brand--cover .brand-mark { width: 74px; height: 74px; }
  .brand--cover .brand-name { font-size: 17px; margin-top: 9px; }
  .cover-url { margin-top: 10px; font-size: 7.5px; letter-spacing: 0.22em; color: var(--ink); }
  .cover-rule { margin-top: 5px; width: 75px; height: 1px; background: var(--tan); }

  .brand--panel { left: 168px; top: 200px; }
  .brand--panel .brand-mark { width: 48px; height: 48px; }
  .brand--panel .brand-name { font-size: 10.5px; margin-top: 6px; }

  .brand--sign { left: 218px; top: 349px; }
  .brand--sign .brand-mark { width: 24px; height: 24px; }
  .brand--sign .brand-name { font-size: 5px; margin-top: 3px; }

  .brand--letter { left: 166px; top: 26px; }
  .brand--letter .brand-mark { width: 43px; height: 43px; }
  .brand--letter .brand-name { font-size: 9.5px; margin-top: 5px; }

  .icon { fill: currentColor; }

  /* Front contact column */
  .contact-stack { position: absolute; left: 0; width: 330px; top: 286px; color: var(--paper); display: flex; flex-direction: column; align-items: center; font-size: 7px; font-weight: 700; }
  .contact-stack .icon { width: 8px; height: 8px; margin-bottom: 3px; }
  .contact-stack .contact-item { display: flex; flex-direction: column; align-items: center; margin-bottom: 7px; }
  .social-row { display: flex; gap: 18px; margin-top: 9px; }
  .social-dot { width: 13px; height: 13px; border-radius: 50%; background: var(--paper); }

  /* Cover letter */
  .cover-letter { position: absolute; left: 24px; top: 20px; width: 290px; color: var(--paper); font-size: 7.4px; line-height: 10.1px; text-align: justify; hyphens: auto; }
  .cover-letter .salutation { font-weight: 700; color: var(--ink); margin-bottom: 6px; font-size: 8px; }
  .signoff { position: absolute; left: 195px; top: 289px; color: var(--ink); font-weight: 700; font-size: 7.8px; line-height: 11px; }
  .signoff .signer { margin-top: 10px; }

  .contact-list { position: absolute; left: 178px; top: 391px; color: var(--paper); font-size: 7px; line-height: 8.6px; list-style: none; }
  .contact-list li { display: flex; align-items: flex-start; gap: 5px; margin-bottom: 7.5px; }
  .contact-list li:last-child { margin-bottom: 0; }
  .contact-list .icon { width: 7px; height: 7px; flex: none; margin-top: 1px; color: var(--ink); }

  /* Pocket */
  .card-slot { position: absolute; left: 363px; top: 381px; width: 133px; height: 70px; background: var(--paper); box-shadow: 1px 2px 3px rgba(0,0,0,0.4); display: flex; align-items: center; justify-content: center; font-size: 7px; color: var(--ink); }
  .slot-tab { position: absolute; width: 12px; height: 3px; background: var(--tan); }
  .slot-tab--tl { left: 358px; top: 381px; transform: rotate(-45deg); }
  .slot-tab--br { left: 487px; top: 448px; transform: rotate(-45deg); }

  /* Letterhead footer */
  .letter-contact { position: absolute; left: 0; width: 100%; top: 378px; color: var(--paper); display: flex; flex-direction: column; align-items: center; font-size: 4.4px; }
  .letter-contact .icon { width: 5px; height: 5px; color: var(--ink); margin-bottom: 1px; }
  .letter-contact span { margin-bottom: 3px; }
  .letter-contact .address { font-weight: 700; margin-top: 1px; }
</style>
</head>
<body>

<svg width="0" height="0" style="position:absolute">
  <defs>
    <symbol id="i-phone" viewBox="0 0 16 16"><path d="M3 1h3l1.5 4-2 1.3a9 9 0 0 0 4.2 4.2L11 8.5l4 1.5v3a2 2 0 0 1-2 2A13 13 0 0 1 1 3a2 2 0 0 1 2-2z"/></symbol>
    <symbol id="i-fax" viewBox="0 0 16 16"><path d="M4 1h8v4H4zM1 6h14v7h-3v-3H4v3H1zM5 11h6v4H5z"/></symbol>
    <symbol id="i-globe" viewBox="0 0 16 16"><path d="M8 1a7 7 0 1 0 0 14A7 7 0 0 0 8 1zm0 1.5c1 1.2 1.7 3 1.8 4.7H6.2C6.3 5.5 7 3.7 8 2.5zM2.6 7.2a5.5 5.5 0 0 1 2.6-4 9 9 0 0 0-.9 4zm0 1.6h1.7a9 9 0 0 0 .9 4 5.5 5.5 0 0 1-2.6-4zm3.6 0h3.6c-.1 1.7-.8 3.5-1.8 4.7-1-1.2-1.7-3-1.8-4.7zm4.6 4a9 9 0 0 0 .9-4h1.7a5.5 5.5 0 0 1-2.6 4zm.9-5.6a9 9 0 0 0-.9-4 5.5 5.5 0 0 1 2.6 4z"/></symbol>
    <symbol id="i-mail" viewBox="0 0 16 16"><path d="M1 3h14v10H1zM2.5 4.5 8 9l5.5-4.5v-.1h-11z"/></symbol>
    <symbol id="i-pin" viewBox="0 0 16 16"><path d="M8 0a5.5 5.5 0 0 0-5.5 5.5C2.5 10 8 16 8 16s5.5-6 5.5-10.5A5.5 5.5 0 0 0 8 0zm0 8a2.5 2.5 0 1 1 0-5 2.5 2.5 0 0 1 0 5z"/></symbol>
  </defs>
</svg>

<p class="view-label view-label--front">front side of the brouchure</p>
<p class="view-label view-label--back">back side of the brouchure</p>
<p class="view-label view-label--letterhead">letter head</p>

<!-- Front of brochure -->
<section class="sheet brochure brochure--front">
  <div class="panel-tan"></div>
  <svg class="deco" viewBox="0 0 658 468" aria-hidden="true">
    <polyline points="135,0 135,58 23,140 0,124" fill="none" stroke="var(--tan-light)" stroke-width="9"/>
    <polygon points="373,0 373,46 439,86 506,41 506,0" fill="var(--tan)"/>
    <polyline points="250,0 250,30 334,94 422,30 422,0" fill="none" stroke="var(--ink)" stroke-width="1.6"/>
    <polygon points="445,468 445,445 550,369 658,449 658,468" fill="var(--tan)"/>
    <polyline points="537,468 537,429 614,374 658,406" fill="none" stroke="var(--ink)" stroke-width="1.6"/>
  </svg>

  <div class="brand brand--panel">
    <div class="brand-mark"></div>
    <div class="brand-name">Bramblewick<br>Homes</div>
  </div>

  <div class="contact-stack">
    <div class="contact-item"><svg class="icon"><use href="#i-phone"/></svg>555-014-0123</div>
    <div class="contact-item"><svg class="icon"><use href="#i-fax"/></svg>555-014-0155</div>
    <div class="contact-item"><svg class="icon"><use href="#i-globe"/></svg>www.bramblewickhomestarrow.com</div>
    <div class="contact-item"><svg class="icon"><use href="#i-mail"/></svg>info@bramblewickhomestarrow.com</div>
    <div class="contact-item"><svg class="icon"><use href="#i-pin"/></svg>88 fernhollow rd. tarrow-on-the-bay, ontario, x0x 0x0.</div>
    <div class="social-row"><span class="social-dot"></span><span class="social-dot"></span></div>
  </div>

  <div class="brand brand--cover">
    <div class="brand-mark"></div>
    <div class="brand-name">Bramblewick<br>Homes</div>
    <div class="cover-url">www.bramblewickhomestarrow.com</div>
    <div class="cover-rule"></div>
  </div>
</section>

<!-- Back of brochure -->
<section class="sheet brochure brochure--back">
  <div class="panel-tan"></div>
  <svg class="deco" viewBox="0 0 658 470" aria-hidden="true">
    <polygon points="32,470 32,423 95,387 159,423 159,470" fill="var(--tan-light)"/>
    <polyline points="0,367 95,435 95,470" fill="none" stroke="var(--ink)" stroke-width="1.6"/>
    <path d="M330,470 V380 A40,40 0 0 1 370,340 H658 V470 Z" fill="var(--charcoal)"/>
    <polygon points="519,340 519,387 589,434 658,383 658,340" fill="var(--tan)"/>
    <polyline points="579,340 579,371 639,421 658,407" fill="none" stroke="var(--paper)" stroke-width="1.6"/>
  </svg>

  <article class="cover-letter">
    <p class="salutation">Dear Sir/Madam:</p>
    <p>Welcome to the new vision of home building in Tarrow. For too long, the building and development business has been saddled with a poor image. Cost overruns, missed deadlines, and poor workmanship has led to most consumers feeling uneasy on building a new home. Unfortunately, in most cases, this image is warranted.</p>
    <p>When we started The Bramblewick Group in 1992, we vowed do our utmost to dispel the industry of this negative rap. We wanted to make honesty, solid workmanship, and above all, excellent service our hallmarks.</p>
    <p>Quite often, the language used by builders to describe their homes can be difficult for consumers to understand. At Bramblewick Homes, we value the opportunity to sit down with each and every client to explain any confusion terminology, as well as absorb as much input as we can from you, the purchaser. Furthermore, this ensures that there are no misconceptions or misunderstandings that exist between us and our clients before executing any contract. We go to great lengths to maintain our hallmarks and to ensure that we have nothing but satisfied customers.</p>
    <p>There couldn't be a better time to build a new home in the Tarrow Region. Industries are booming, and the beautiful landscape this region has to offer has led to new citizens flocking down here in recent years. From the wineries and restaurants to the picturesque views and kind neighbors, the region of Tarrow has become a desirable spot for families of all types.</p>
    <p>The time is now to make your dreams a reality. We look forward to the opportunity to build your dream home in the near future, and if you have any questions, please do not hesitate to ask myself, or a member of my staff.</p>
  </article>

  <div class="signoff">
    <p>Yours truly,</p>
    <p class="signer">Marcel Ondrey<br>Founder and President</p>
  </div>

  <div class="brand brand--sign">
    <div class="brand-mark"></div>
    <div class="brand-name">Bramblewick<br>Homes</div>
  </div>

  <ul class="contact-list">
    <li><svg class="icon"><use href="#i-phone"/></svg>555-014-0123</li>
    <li><svg class="icon"><use href="#i-fax"/></svg>555-014-0155</li>
    <li><svg class="icon"><use href="#i-globe"/></svg>www.bramblewickhomestarrow.com</li>
    <li><svg class="icon"><use href="#i-pin"/></svg><span>88 fernhollow rd. tarrow-on-the-bay,<br>ontario, x0x 0x0.</span></li>
  </ul>

  <div class="card-slot">your business card goes here</div>
  <span class="slot-tab slot-tab--tl"></span>
  <span class="slot-tab slot-tab--br"></span>
</section>

<!-- Letterhead -->
<section class="sheet letterhead">
  <svg class="deco" viewBox="0 0 333 469" aria-hidden="true">
    <polygon points="0,469 0,438 170,357 333,432 333,469" fill="var(--tan)"/>
    <polyline points="255,469 255,427 327,381 333,387" fill="none" stroke="var(--ink)" stroke-width="1.4"/>
  </svg>

  <div class="brand brand--letter">
    <div class="brand-mark"></div>
    <div class="brand-name">Bramblewick<br>Homes</div>
  </div>

  <div class="letter-contact">
    <svg class="icon"><use href="#i-phone"/></svg><span>555-014-0123</span>
    <svg class="icon"><use href="#i-fax"/></svg><span>555-014-0155</span>
    <svg class="icon"><use href="#i-globe"/></svg><span>www.bramblewickhomestarrow.com</span>
    <svg class="icon"><use href="#i-pin"/></svg><span class="address">88 FERNHOLLOW RD. TARROW-ON-THE-BAY, ONTARIO, X0X 0X0</span>
  </div>
</section>

</body>
</html>
```